We Buy Houses Postcard Design

Harborline Asset Partners is one of Baltimore‘s top real estate investing groups because we treat buyers and sellers like real people; not like numbers on a spreadsheet. We specialize in buying distressed properties including multi-family, commercial, retail, single family, and bank REO’s from sellers who need to sell fast. Our website is www.harborlineassetpartners.com. Our phone number is (555) 274-1916. Both need to be on the card. Front and back sides are to be printed. Front full color, back black and white. We want our logo on the design somewhere. The logo can be found on the website. If you need the original files ask me for them. See attached as examples. Return address should be 587 W Tessaly Ave, Suite 319, Baltimore, MD 21209. My name is Marcus. Address label is 1" x 2-5/8". Please leave room for it and postage on the back side.

Industry/Entity Type

Real Estate

```html
<!DOCTYPE html>
<html lang="en">
<head>
<meta charset="utf-8">
<title>Harborline Asset Partners – We Buy Houses Postcard</title>
<link rel="stylesheet" href="https://fonts.googleapis.com/css2?family=Arimo:wght@400;700&display=swap">
<style>
  :root {
    --paper: #ffffff;
    --ink: #111111;
    --brand-blue: #2b2f9c;
    --brand-square: #1e6fd9;
    --highlight: #ffe600;
    --alert-red: #ee1c25;
    --signature-tone: #e9e9e9;
    --white: #ffffff;
  }
  * { box-sizing: border-box; margin: 0; padding: 0; }
  html, body {
    width: 1200px;
    height: 863px;
    overflow: hidden;
    background: var(--paper);
  }
  .postcard {
    position: relative;
    width: 1200px;
    height: 863px;
    background: var(--paper);
    font-family: "Arimo", Arial, sans-serif;
    color: var(--ink);
    letter-spacing: 2.2px;
  }
  .brand {
    position: absolute;
    left: 64px;
    top: 58px;
    display: flex;
    align-items: center;
    gap: 16px;
  }
  .brand-square {
    width: 58px;
    height: 58px;
    background: var(--brand-square);
  }
  .brand-name {
    font-size: 34px;
    font-weight: 700;
    line-height: 1.05;
    color: var(--brand-blue);
    letter-spacing: 0.5px;
    text-transform: uppercase;
  }
  .line {
    position: absolute;
    left: 65px;
    font-size: 24px;
    line-height: 1;
    white-space: nowrap;
  }
  .greeting { top: 211px; }
  .highlight {
    position: absolute;
    left: 65px;
    top: 246px;
    width: 488px;
    height: 42px;
    background: var(--highlight);
    font-size: 24px;
    line-height: 42px;
    padding-left: 2px;
    white-space: nowrap;
  }
  .benefits {
    position: absolute;
    left: 65px;
    top: 316px;
    width: 546px;
    height: 180px;
  }
  .benefits-frame {
    position: absolute;
    inset: 0;
  }
  .benefits-list {
    position: absolute;
    left: 25px;
    top: 9px;
    list-style: none;
    font-size: 24px;
    line-height: 42px;
    white-space: nowrap;
  }
  .closing-1 { top: 527px; }
  .closing-2 { top: 569px; }
  .closing-3 { top: 614px; }
  .signature {
    position: absolute;
    left: 66px;
    top: 664px;
    width: 126px;
    height: 38px;
    background: var(--signature-tone);
    border-radius: 4px;
  }
  .contact {
    position: absolute;
    left: 65px;
    top: 717px;
    font-size: 17.5px;
    line-height: 27.5px;
    letter-spacing: 1.5px;
    white-space: nowrap;
    font-style: normal;
  }
  .contact-phone {
    font-size: 24px;
    font-weight: 700;
    letter-spacing: 2.4px;
    margin-top: 2px;
    margin-left: -1px;
  }
  .urgent-badge {
    position: absolute;
    left: 612px;
    top: 694px;
    width: 535px;
    height: 92px;
    background: var(--alert-red);
    color: var(--white);
    font-size: 44px;
    font-weight: 700;
    letter-spacing: 3.6px;
    text-align: center;
    line-height: 92px;
  }
</style>
</head>
<body>
  <main class="postcard">
    <header class="brand">
      <span class="brand-square"></span>
      <span class="brand-name">Harborline<br>Asset Partners</span>
    </header>

    <p class="line greeting">My name is Marcus.</p>
    <p class="highlight">I am interested in buying your house!</p>

    <section class="benefits">
      <svg class="benefits-frame" width="546" height="180" viewBox="0 0 546 180" aria-hidden="true">
        <path d="M4 5 L541 2 L543 176 L5 177 Z" fill="none" stroke="#ee1c25" stroke-width="4.5" stroke-linejoin="round"/>
      </svg>
      <ul class="benefits-list">
        <li>- CASH for your house ‘‘AS-IS’’</li>
        <li>- No inspactions or contingencies</li>
        <li>- Fast and lexible closing</li>
        <li>- No need to fix or clean out your home</li>
      </ul>
    </section>

    <p class="line closing-1">There are never any obligations.</p>
    <p class="line closing-2">If you’re interested, please contact us.</p>
    <p class="line closing-3">We look forward to hearing from you!</p>

    <div class="signature" role="img" aria-label="Handwritten signature of Marcus"></div>

    <address class="contact">
      <div class="contact-company">Harborline Asset Partners, LLC</div>
      <div class="contact-web">www.harborlineassetpartners.com</div>
      <div class="contact-address">587 W Tessaly Ave, Suite 319, Baltimore, MD 21209</div>
      <div class="contact-phone">(555) 274-1916</div>
    </address>

    <div class="urgent-badge">URGENT NOTICE</div>
  </main>
</body>
</html>
```